Multiple Page Flyer -6 pager

Looking for an attractive new flyer for our synthetic greens and turf division. Please use our new logo attached and theme around the logo and use lots of pictures from the website. Pick the best from

I envision the following:
Page 1: Cover page
Page 2: Golfing Greens
Page 3: Golfing Greens 2
Page 4: Artificial Lawns 50% / Pet Turf 50%
Page 5: Pet Turf 50% / Playgrounds 50%
Page 6: Sports

```html
<!DOCTYPE html>
<html lang="en">
<head>
<meta charset="utf-8">
<title>Turf Flyer – Artificial Lawns &amp; Pet Turf</title>
<link rel="stylesheet" href="https://fonts.googleapis.com/css2?family=Source+Sans+3:wght@300;400&display=swap">
<style>
  :root {
    --backdrop: #636466;
    --grass-dark: #1f4a17;
    --grass-mid: #2f7a22;
    --grass-light: #4fa33a;
    --panel: rgba(20, 48, 16, 0.55);
    --text: #ffffff;
    --caption: #0e2a0b;
    --dog-tone-a: #e9e6df;
    --dog-tone-b: #3d6a2a;
    --lawn-tone-a: #b9a58c;
    --lawn-tone-b: #3f7d2c;
  }
  * { box-sizing: border-box; margin: 0; padding: 0; }
  html, body { width: 1200px; height: 1200px; overflow: hidden; }
  body {
    background: var(--backdrop);
    font-family: "Source Sans 3", "Myriad Pro", sans-serif;
    font-weight: 300;
    color: var(--text);
    position: relative;
  }
  .flyer-page {
    position: absolute;
    left: 204px; top: 40px;
    width: 792px; height: 1120px;
    overflow: hidden;
  }
  .grass-field {
    position: absolute; inset: 0;
    background:
      radial-gradient(circle at 20% 15%, var(--grass-light) 0%, transparent 40%),
      radial-gradient(circle at 80% 70%, var(--grass-light) 0%, transparent 45%),
      linear-gradient(160deg, var(--grass-mid), var(--grass-dark) 55%, var(--grass-mid));
  }
  .text-panel {
    position: absolute;
    background: var(--panel);
  }
  .panel-intro { left: 44px; top: 100px; width: 703px; height: 447px; }
  .panel-outro { left: 329px; top: 753px; width: 410px; height: 302px; }
  .photo-circle {
    position: absolute;
    border-radius: 50%;
  }
  .photo-dog {
    left: 416px; top: 368px; width: 350px; height: 350px;
    background: linear-gradient(180deg, var(--dog-tone-a) 0%, var(--dog-tone-a) 35%, var(--dog-tone-b) 60%, var(--grass-dark) 100%);
  }
  .photo-lawn {
    left: 15px; top: 636px; width: 350px; height: 350px;
    background: linear-gradient(180deg, var(--lawn-tone-a) 0%, var(--lawn-tone-a) 22%, var(--lawn-tone-b) 40%, var(--grass-dark) 100%);
  }
  .photo-caption {
    position: absolute; left: 568px; top: 720px;
    font-size: 12px; color: var(--caption); font-weight: 400;
  }
  .copy {
    position: absolute;
    font-size: 14px; line-height: 20px;
  }
  .copy p + p { margin-top: 20px; }
  .copy-intro { left: 79px; top: 120px; width: 650px; }
  .copy-intro .narrow { width: 360px; }
  .copy-outro { left: 375px; top: 786px; width: 355px; line-height: 25px; }
  .drop-cap {
    float: left;
    font-size: 62px; line-height: 50px;
    margin: 4px 2px 0 0;
    font-weight: 400;
  }
  .brand-name { font-size: 18px; font-weight: 400; }
</style>
</head>
<body>
  <main class="flyer-page">
    <div class="grass-field" role="img" aria-label="Close-up texture of green turf blades filling the page"></div>

    <div class="text-panel panel-intro"></div>
    <div class="text-panel panel-outro"></div>

    <section class="copy copy-intro">
      <p><span class="drop-cap">W</span>e love our pets, and we can’t imagine life without them. However, no one likes a yard full of bare or brown spots, and no one likes muddy paws tracking dirt and debris through the house. Many a pet owner has daydreamed about a life with a perfect lawn and their furry friend at their side. Now that dream can be a reality with beautiful, low maintenance pet lawns from <span class="brand-name">Evergreen Turf Works</span> – your source for the best artificial lawn installation services in Harbor City and the surrounding areas.</p>
      <p>Let’s get the obvious question out of the way first – you’re probably wondering how artificial turf can possibly handle the daily “duties” of a dog. The answer is simple: our beautiful, low maintenance turf and grass is designed for optimal drainage, which is the key to preventing odors and removing liquid waste promptly. In fact, the drainage of our artificial lawns is often far superior to the drainage of common grass lawns.</p>
      <p class="narrow">The base substrate we install below the artificial turf is also specifically designed to function well for pet owners. The addition of odor-absorbing material to the turf eliminates the smell caused by dog urine, keeping it dormant before being washed away during the next rain.</p>
    </section>

    <div class="photo-circle photo-dog" role="img" aria-label="Photo of a black and white puppy chewing a yellow toy on artificial grass"></div>
    <span class="photo-caption">Lorem ipsum</span>

    <div class="photo-circle photo-lawn" role="img" aria-label="Photo of a backyard artificial lawn with a curved stone path and wooden fence"></div>

    <section class="copy copy-outro">
      <p><span class="drop-cap">A</span>rtificial grass eliminates the need for mowing, trimming, watering and fertilizing. This low maintenance solution will stay beautiful all year long. We have a passion for creating beautiful landscapes for business and homes for over 45 years. We truly understand each job and vision is unique and take great pride in all of our work. Let us help transform your residential or commercial property today.</p>
    </section>
  </main>
</body>
</html>
```